Business Cards

Need business card design that I can update for new employees and details. Needs to incorporate our logo, be bright and fun (in line with tourism and holidays)
Would like a Map of Western Australia on the front with locations all the caravan parks we own (just purchased Tom Price so please include that as well as others listed on our website).
Target Market(s)
Famillies
Contact Information for Business Card
5 Cards -
Neil Perrow (Director) e: perrow@wattlebay.com.au p: 0491 570 156
Mira Perrow (Director) e: perrow@wattlebay.com.au p: 0491 570 157
Owen Halvey (General Manager) e: halvey@wattlebay.com.au p: 0491 570 158
Helen Halvey (General Manager) e: halvey@wattlebay.com.au p: 0491 570 159
Colin Danby (Training and Operations Manager) - e: danby@wattlebay.com.au p:0491 570 110
Colors
Look and feel

```html
<!DOCTYPE html>
<html lang="en">
<head>
<meta charset="utf-8">
<title>Wattle Bay Tourist Parks – Business Card</title>
<link rel="stylesheet" href="https://fonts.googleapis.com/css2?family=Cormorant+Garamond:wght@500;600&family=Open+Sans:wght@400&display=swap">
<style>
  :root {
    --backdrop: #ebe8e5;
    --card-teal: #41c0cb;
    --card-white: #ffffff;
    --card-grey: #e5e5e5;
    --ink-grey: #555759;
    --mark-teal: #41c0cb;
    --accent-green: #6abfad;
    --accent-mint: #b9e2dc;
    --serif: "Cormorant Garamond", "Times New Roman", serif;
    --sans: "Open Sans", Arial, sans-serif;
  }
  * { box-sizing: border-box; margin: 0; padding: 0; }
  html, body { width: 1200px; height: 900px; overflow: hidden; }
  body { background: var(--backdrop); position: relative; }

  .card { position: absolute; overflow: hidden; }

  /* Front card */
  .card-front {
    left: 169px; top: 54px; width: 589px; height: 364px;
    background: var(--card-teal);
    color: var(--card-white);
  }
  .feature-graphic {
    position: absolute; left: 0; top: 0; width: 295px; height: 364px;
    background: linear-gradient(155deg, var(--accent-green) 0%, var(--accent-mint) 55%, var(--card-white) 100%);
  }
  .card-front .bottom-band {
    position: absolute; left: 0; bottom: 0; width: 100%; height: 20px;
    background: var(--card-white);
  }
  .brand-front {
    position: absolute; right: 36px; top: 42px; text-align: center;
    font-family: var(--serif); font-weight: 600;
  }
  .brand-front .brand-name {
    font-size: 41px; letter-spacing: 3px; font-variant: small-caps; line-height: 1;
  }
  .brand-front .brand-tagline {
    font-size: 16px; letter-spacing: 3.5px; text-transform: uppercase; margin-top: 8px;
  }
  .person {
    position: absolute; right: 36px; top: 172px; text-align: right;
  }
  .person-name {
    font-family: var(--serif); font-weight: 600; font-size: 25px; letter-spacing: 0.5px;
    text-transform: uppercase; line-height: 1.1;
  }
  .person-role {
    font-family: var(--sans); font-size: 14.5px; margin-top: 4px;
  }
  .contact {
    position: absolute; right: 36px; top: 243px; text-align: right;
    font-family: var(--sans); font-size: 15.5px; line-height: 22px;
  }
  .contact-line { display: flex; justify-content: flex-end; align-items: center; gap: 4px; }
  .contact-line svg { width: 14px; height: 14px; fill: var(--card-white); }

  /* Back card */
  .card-back {
    left: 388px; top: 505px; width: 567px; height: 352px;
    background: var(--card-grey);
  }
  .brand-mark {
    position: absolute; left: 232px; top: 95px; width: 104px; height: 104px;
    background: var(--mark-teal);
  }
  .brand-back {
    position: absolute; left: 0; top: 186px; width: 100%; text-align: center;
    font-family: var(--serif); font-weight: 600; color: var(--ink-grey);
  }
  .brand-back .brand-name {
    font-size: 52px; letter-spacing: 5px; font-variant: small-caps; line-height: 1;
  }
  .brand-back .brand-tagline {
    font-size: 20px; letter-spacing: 4.5px; text-transform: uppercase; margin-top: 8px;
  }
</style>
</head>
<body>

  <section class="card card-front" aria-label="Business card front">
    <div class="feature-graphic" role="img" aria-label="Large brand sunburst over a rolling hill, green and white"></div>

    <div class="brand-front">
      <div class="brand-name">Wattle Bay</div>
      <div class="brand-tagline">Tourist Parks</div>
    </div>

    <div class="person">
      <div class="person-name">Neil Perrow</div>
      <div class="person-role">Director</div>
    </div>

    <div class="contact">
      <div class="contact-line">
        <span>0491 570 156</span>
        <svg viewBox="0 0 24 24" aria-hidden="true"><path d="M6.6 10.8a15.1 15.1 0 0 0 6.6 6.6l2.2-2.2a1 1 0 0 1 1-.25 11.4 11.4 0 0 0 3.6.57 1 1 0 0 1 1 1V20a1 1 0 0 1-1 1A17 17 0 0 1 3 4a1 1 0 0 1 1-1h3.5a1 1 0 0 1 1 1c0 1.250.2 2.450.57 3.570a1 1 0 0 1-.25 1z"/></svg>
      </div>
      <div class="contact-line">
        <span>perrow@wattlebay.com.au</span>
        <svg viewBox="0 0 24 24" aria-hidden="true"><path d="M2 5h20v14H2z" fill="var(--card-white)"/><path d="M2 5l10 8 10-8" fill="none" stroke="var(--card-teal)" stroke-width="1.8"/></svg>
      </div>
    </div>

    <div class="bottom-band"></div>
  </section>

  <section class="card card-back" aria-label="Business card back">
    <div class="brand-mark" aria-hidden="true"></div>
    <div class="brand-back">
      <div class="brand-name">Wattle Bay</div>
      <div class="brand-tagline">Tourist Parks</div>
    </div>
  </section>

</body>
</html>
```